We need a Welcome Booklet designed for our Church - Harrowgate Fields Church. We would like a design that is contemporary with no religious symbols or old pictures. Please use quality contemporary photos . See attached a Word document with what content we want in the booklet.

Target Market(s)

Guests to the church so new person friendly

Requirements
Must have
• A contemporary modern look
Should not have
• Religious symbols or old pictures

```html
<!DOCTYPE html>
<html lang="en">
<head>
<meta charset="utf-8">
<title>Harrowgate Fields Church – Get Connected</title>
<link rel="stylesheet" href="https://fonts.googleapis.com/css2?family=Bitter:wght@300;400&family=Didact+Gothic&family=Questrial&display=swap">
<style>
  :root {
    --paper: #ffffff;
    --ink: #1e1e1e;
    --hero-dark: #14182a;
    --hero-warm: #6b5a48;
    --accent-purple: #8f2fe0;
    --accent-red: #e5161b;
    --accent-orange: #f7941d;
    --photo-wall: #3a5a5c;
    --photo-warm: #8c6a58;
  }
  * { margin: 0; padding: 0; box-sizing: border-box; }
  html, body { width: 855px; height: 1200px; overflow: hidden; background: var(--paper); }
  .page {
    position: relative; width: 855px; height: 1200px; overflow: hidden;
    color: var(--ink);
    font-family: "Didact Gothic", "Questrial", sans-serif;
    font-size: 22px; line-height: 28.2px;
  }
  .line { display: block; white-space: nowrap; }
  .justified .line { text-align: justify; text-align-last: justify; }
  .justified .line.last { text-align-last: left; }

  .hero {
    position: absolute; left: 0; top: 0; width: 855px; height: 201px;
    background:
      radial-gradient(ellipse at 14% 45%, rgba(70,120,230,.75), transparent 40%),
      radial-gradient(ellipse at 70% 30%, rgba(150,120,90,.55), transparent 55%),
      linear-gradient(180deg, #0f1322 0%, var(--hero-warm) 55%, var(--hero-dark) 100%);
  }
  .hero-title {
    position: absolute; left: 52px; top: 100px;
    font-family: "Bitter", serif; font-weight: 300;
    font-size: 45px; line-height: 46px; color: #fff; white-space: nowrap;
  }

  .intro, .welcome { position: absolute; left: 56px; width: 742px; }
  .intro { top: 237px; }
  .welcome { top: 434px; }

  .link-purple { color: var(--accent-purple); font-weight: 700; font-family: "Questrial", sans-serif; }
  .link-red { color: var(--accent-red); font-weight: 700; font-family: "Questrial", sans-serif; }

  .more-info { position: absolute; left: 56px; top: 612px; width: 320px; }

  .team-photo {
    position: absolute; left: 378px; top: 614px; width: 434px; height: 253px;
    background: linear-gradient(180deg, var(--photo-wall) 0%, #4b4a52 50%, var(--photo-warm) 100%);
  }

  .serve-title {
    position: absolute; left: 53px; top: 800px;
    font-family: "Bitter", serif; font-weight: 400;
    font-size: 46px; line-height: 44px; white-space: nowrap;
  }
  .serve-text { position: absolute; left: 54px; top: 907px; width: 640px; }

  .team-badge {
    position: absolute; left: 627px; top: 839px; width: 168px; height: 168px;
    border-radius: 50%; background: var(--accent-orange);
    display: flex; align-items: center; justify-content: center; text-align: center;
    color: #fff; font-family: "Questrial", sans-serif; font-weight: 700;
    font-size: 26px; line-height: 33px;
  }

  .serve-more { position: absolute; left: 54px; top: 1094px; width: 720px; }
</style>
</head>
<body>
<main class="page">
  <header class="hero" role="img" aria-label="Photo of a packed auditorium during a church gathering, lit in blue stage light">
    <h1 class="hero-title">Join a life group or<br>attend one of our courses</h1>
  </header>

  <p class="intro justified">
    <span class="line">Our various Life Groups are located in different parts of the city and</span>
    <span class="line">they meet every fortnight or once a month. We run various courses in</span>
    <span class="line">the year that will set you on a journey to discover faith and help you</span>
    <span class="line">live in the will of God. There will be something that you will find enrich-</span>
    <span class="line">ing. As you connect to a group or attend a course you will find enrich-</span>
    <span class="line last">ing teaching but also build great friendships and grow as a person.</span>
  </p>

  <p class="welcome justified">
    <span class="line">For our new members, a great start would be for you to attend <span class="link-purple">HFC</span></span>
    <span class="line"><span class="link-purple">Life course</span>. We would love to get to know you and help you settle into</span>
    <span class="line">the HFC family. If you would to join a Life Group, please come along</span>
    <span class="line">to our <span class="link-purple">Central Life Group</span> which takes place here at the church on</span>
    <span class="line last">Wednesdays from 7:30- 9:00pm.</span>
  </p>

  <p class="more-info">
    <span class="line">To find out more about</span>
    <span class="line">our Life Groups, please</span>
    <span class="line">visit: - <span class="link-red">hfc.church/life-groups</span></span>
    <span class="line">and for more information</span>
    <span class="line">about our courses, please</span>
    <span class="line">visit:- <span class="link-red">hfc.church/courses</span></span>
  </p>

  <div class="team-photo" role="img" aria-label="Photo of a smiling group of friends standing together in front of a chalkboard wall"></div>

  <h2 class="serve-title">Serve<br>on a team</h2>

  <p class="serve-text">
    <span class="line">Sunday services, Foodbank, Children’s work, Youth</span>
    <span class="line">teams, drama group- our church could not happen</span>
    <span class="line">without you!! Being part of a team is a great way to</span>
    <span class="line">meet people and actually make a difference in the</span>
    <span class="line">life of our church. You are literally making the vision of the</span>
    <span class="line">church happen by serving with us.</span>
  </p>

  <div class="team-badge">Church<br>is a team<br>sport!</div>

  <p class="serve-more">
    <span class="line">For more information on how you can get involved in any of our</span>
    <span class="line">serving teams, please visit: - <span class="link-red">hfc.church/serve</span></span>
  </p>
</main>
</body>
</html>
```